Plotvista Caribbean

We need a vibrant, user friendly and exciting website for our land search company called "plotVista" This application will help individuals locate and or list lots for sale within the Caribbean. We will offer a small cash back incentive to buyers that purchase land from our site, and we will charge a 1%-2% success fee to our sellers once a successful transaction is made. We would like to become a match making site, matching buyers and sellers on our platform. We will also include a service directory and marketing advertisement spot for other service providers for a fee. We would like to see a webdesign incorporating Caribbean colors (blue, green and yellow) with very modern clean lines, very picturesque and easy to use.

Industry/Entity Type

Real Estate

Coding

Coded - Design and coding required

Number of Pages Required

5+ page

Font styles to use
Sans Serif

Colors
ffffff
85acd3
b768aa
dbdbdb

Requirements
Nice to have
• Scenic photos of the ocean and beautiful landscape

```html
<!DOCTYPE html>
<html lang="en">
<head>
<meta charset="utf-8">
<title>plotVista — Caribbean Land Search</title>
<link href="https://fonts.googleapis.com/css2?family=Nunito+Sans:wght@400;600;700&family=Open+Sans:wght@400;600&display=swap" rel="stylesheet">
<style>
:root{
  --purple:#b768aa;
  --blue:#85acd3;
  --grey:#dbdbdb;
  --white:#ffffff;
  --ink:#1e1e1e;
  --body:#666666;
  --footer:#111111;
  --sea-deep:#0f4f86;
  --sea:#1f7fa6;
  --green:#2f5d2b;
}
*{box-sizing:border-box;margin:0;padding:0}
html,body{width:1200px;height:2671px;overflow:hidden;background:var(--white)}
body{font-family:"Open Sans",Arial,sans-serif;color:var(--ink);position:relative}
.heading{font-family:"Nunito Sans",Arial,sans-serif}

/* Hero */
.hero{position:absolute;left:0;top:0;width:1200px;height:507px;
  background:linear-gradient(180deg,#5f7f9c 0%,#1d5f94 22%,var(--sea-deep) 48%,#2e6a3a 72%,var(--green) 100%)}
.brand{position:absolute;left:98px;top:30px;font-family:"Nunito Sans",sans-serif;font-weight:600;font-size:29px;color:var(--white)}
.top-phone{position:absolute;right:98px;top:12px;display:flex;align-items:center;gap:10px;color:var(--white);font-size:17px}
.icon-ring{width:32px;height:32px;border:1.5px solid var(--white);border-radius:50%;display:flex;align-items:center;justify-content:center}
.main-nav{position:absolute;left:385px;top:56px;display:flex;gap:29px;font-family:"Nunito Sans",sans-serif;font-weight:600;font-size:16px;color:var(--white)}
.main-nav .active{color:var(--purple)}
.hero-title{position:absolute;left:0;right:0;top:122px;text-align:center;font-family:"Nunito Sans",sans-serif;font-weight:600;font-size:66px;color:var(--white)}
.hero-sub{position:absolute;left:0;right:0;top:220px;text-align:center;font-family:"Nunito Sans",sans-serif;font-weight:600;font-size:24px;color:var(--white)}
.search{position:absolute;left:308px;top:280px;display:flex;height:50px}
.search-input{width:457px;background:var(--white);font-size:14px;color:#777;display:flex;align-items:center;padding-left:20px}
.search-btn{width:127px;background:var(--purple);color:var(--white);font-family:"Nunito Sans",sans-serif;font-weight:700;font-size:16px;display:flex;align-items:center;justify-content:center;letter-spacing:.5px}
.dots{position:absolute;left:568px;top:446px;display:flex;gap:5px}
.dots span{width:11px;height:11px;border-radius:50%;border:1.5px solid var(--white)}
.dots .on{background:var(--white)}

/* Welcome */
.welcome-title{position:absolute;left:98px;top:556px;font-size:28px;font-weight:600}
.welcome-text{position:absolute;left:98px;top:620px;width:500px;font-size:12.5px;line-height:24px;color:var(--body)}
.welcome-text p+p{margin-top:22px}
.btn-outline{position:absolute;border:1.5px solid var(--purple);border-radius:22px;color:var(--purple);font-family:"Nunito Sans",sans-serif;font-weight:700;display:flex;align-items:center;justify-content:center;letter-spacing:.5px}
.read-more{left:98px;top:822px;width:130px;height:37px;font-size:12px}
.map{position:absolute;left:645px;top:566px;width:458px;height:294px;border:4px solid #eeeeee;
  background:linear-gradient(135deg,#a9c6ee 0%,#9fbfe9 55%,#b7cde9 100%)}

/* Banner */
.banner{position:absolute;left:0;top:922px;width:1200px;height:288px;
  background:linear-gradient(180deg,#3d6a4c 0%,#2f8a8a 40%,#138a8e 70%,#0d6f7c 100%);
  display:flex;align-items:center;justify-content:center}
.banner p{width:930px;text-align:center;color:var(--white);font-family:"Nunito Sans",sans-serif;font-weight:600;font-size:25.5px;line-height:41px}

/* Services */
.section-title{position:absolute;left:0;right:0;text-align:center;font-size:29px;font-weight:600}
.services-title{top:1266px}
.services{position:absolute;left:72px;top:1350px;display:flex;width:1056px}
.service{width:264px;text-align:center}
.service svg{display:block;margin:0 auto}
.service h3{font-family:"Nunito Sans",sans-serif;font-weight:600;font-size:19px;margin-top:14px}
.service p{font-size:12.5px;line-height:24px;color:var(--body);margin-top:6px}
.divider{position:absolute;left:98px;top:1684px;width:1004px;height:1px;background:var(--grey)}

/* Destinations */
.featured-title{top:1732px}
.photo{position:absolute}
.photo-resort{left:98px;top:1820px;width:621px;height:453px;background:linear-gradient(180deg,#3c88b8 0%,#8fa7b4 45%,#d9d3c6 80%,#4fc1c0 100%)}
.photo-bay{left:724px;top:1820px;width:378px;height:224px;background:linear-gradient(180deg,#9fc3e0 0%,#6b8c7a 50%,#3fb5b8 80%,#5a7a52 100%)}
.photo-cove{left:724px;top:2050px;width:378px;height:223px;background:linear-gradient(180deg,#dfe6ee 0%,#6e9bc8 35%,#1f6e9a 60%,#4d7b3c 100%)}
.explore{left:508px;top:2320px;width:185px;height:44px;font-size:13px}

/* Footer */
.footer{position:absolute;left:0;top:2438px;width:1200px;height:233px;background:var(--footer);color:var(--white)}
.contact-row{position:absolute;left:288px;top:38px;display:flex;gap:30px;font-size:13px;line-height:22px;align-items:center}
.contact-item{display:flex;align-items:center;gap:16px}
.contact-item .icon-ring{width:44px;height:44px;border-color:#cccccc}
.footer-nav{position:absolute;left:0;right:0;top:110px;text-align:center;font-size:13.5px}
.footer-nav span.sep{margin:0 17px}
.footer-rule{position:absolute;left:98px;top:165px;width:1004px;height:1px;background:#2b2b2b}
.copyright{position:absolute;left:98px;top:192px;font-size:12.5px}
.social{position:absolute;right:88px;top:186px;display:flex;gap:8px}
.social span{width:32px;height:32px;border:1.5px solid var(--white);border-radius:50%}
</style>
</head>
<body>

<header class="hero" role="img" aria-label="Aerial photo of green Caribbean islands in a deep blue sea with sailboats">
  <div class="brand">plotVista</div>
  <div class="top-phone">
    <span class="icon-ring"><svg width="14" height="14" viewBox="0 0 24 24"><path d="M6.6 10.8a15.1 15.1 0 0 0 6.6 6.6l2.2-2.2c.3-.3.7-.4 1-.2 1.1.4 2.3.6 3.6.6.6 0 1 .4 1 1V20c0 .6-.4 1-1 1A17 17 0 0 1 3 4c0-.6.4-1 1-1h3.5c.6 0 1 .4 1 1 0 1.3.2 2.5.6 3.6.1.3 0 .7-.2 1z" fill="#fff"/></svg></span>
    1 555 010 2040
  </div>
  <nav class="main-nav">
    <span class="active">Home</span><span>About</span><span>Buy</span><span>Sell</span><span>Landlords</span><span>Rent</span><span>Our services</span><span>Contact</span>
    <svg width="16" height="16" viewBox="0 0 24 24" style="margin-top:2px"><circle cx="10" cy="10" r="7" fill="none" stroke="#fff" stroke-width="3"/><path d="M15 15l6 6" stroke="#fff" stroke-width="3"/></svg>
  </nav>
  <h1 class="hero-title">plotVista</h1>
  <p class="hero-sub">We help individuals locate and or list lots for sale within the Caribbean.</p>
  <div class="search">
    <div class="search-input">Enter Town or Post Code</div>
    <div class="search-btn">SEARCH</div>
  </div>
  <div class="dots"><span class="on"></span><span></span><span></span><span></span></div>
</header>

<section class="welcome">
  <h2 class="welcome-title heading">Welcome to plotVista</h2>
  <div class="welcome-text">
    <p>At vero eos et accusamus et iusto odio dignissimos ducimus qui blanditiis praesen iuvol up tatum deleniti atque corrupti quos dolores et quas.</p>
    <p>Molestias excepturi sint occaecati cupiditate non provident, similique sunt in culp quise officia deserunt mollitia animi, id est laborum et dolorum fuga. Et harum quidem rerum facilis estet expedita distinctio. Nam libero tempore, cum soluta nobis est eligendi optio cumque nihil im pedit quo minus id quod maxime.</p>
  </div>
  <div class="btn-outline read-more">READ MORE &gt;&gt;</div>
  <div class="map" role="img" aria-label="Map of the Caribbean with a location pin"></div>
</section>

<section class="banner" role="img" aria-label="Turquoise bay with a wooden dock and green shoreline">
  <p>We will offer a small cash back incentive to buyers that purchase land from our site, and we will charge a 1%-2% success fee to our sellers once a successful transaction is made.</p>
</section>

<h2 class="section-title services-title heading">Our Services</h2>
<section class="services">
  <div class="service">
    <svg width="180" height="180" viewBox="0 0 180 180"><rect x="37" y="37" width="106" height="106" transform="rotate(45 90 90)" fill="none" stroke="#b768aa" stroke-width="1.5"/><rect x="43" y="43" width="94" height="94" transform="rotate(45 90 90)" fill="#b768aa"/><rect x="64" y="77" width="52" height="28" rx="2" fill="#fff"/><circle cx="90" cy="91" r="8" fill="#b768aa"/></svg>
    <h3>Buy Now</h3>
    <p>Neque porro quisquam est, qui do<br>lorem ipsum quia dolor sit</p>
  </div>
  <div class="service">
    <svg width="180" height="180" viewBox="0 0 180 180"><rect x="37" y="37" width="106" height="106" transform="rotate(45 90 90)" fill="none" stroke="#b768aa" stroke-width="1.5"/><rect x="43" y="43" width="94" height="94" transform="rotate(45 90 90)" fill="none" stroke="#b768aa" stroke-width="4"/><path d="M70 78h7l5 18h20l5-13H80" fill="none" stroke="#85acd3" stroke-width="4"/><circle cx="85" cy="103" r="3" fill="#85acd3"/><circle cx="100" cy="103" r="3" fill="#85acd3"/></svg>
    <h3>Sell now</h3>
    <p>Neque porro quisquam est, qui do<br>lorem ipsum quia dolor sit</p>
  </div>
  <div class="service">
    <svg width="180" height="180" viewBox="0 0 180 180"><rect x="37" y="37" width="106" height="106" transform="rotate(45 90 90)" fill="none" stroke="#b768aa" stroke-width="1.5"/><rect x="43" y="43" width="94" height="94" transform="rotate(45 90 90)" fill="none" stroke="#b768aa" stroke-width="4"/><rect x="64" y="77" width="52" height="28" rx="2" fill="#85acd3"/><circle cx="90" cy="91" r="8" fill="#fff"/></svg>
    <h3>Make Money</h3>
    <p>Neque porro quisquam est, qui do<br>lorem ipsum quia dolor sit</p>
  </div>
  <div class="service">
    <svg width="180" height="180" viewBox="0 0 180 180"><rect x="37" y="37" width="106" height="106" transform="rotate(45 90 90)" fill="none" stroke="#b768aa" stroke-width="1.5"/><rect x="43" y="43" width="94" height="94" transform="rotate(45 90 90)" fill="none" stroke="#b768aa" stroke-width="4"/><path d="M72 72q-8 20 6 38M80 68q-8 22 6 42M88 66q-8 24 6 44" fill="none" stroke="#85acd3" stroke-width="3"/></svg>
    <h3>Vista Services</h3>
    <p>Neque porro quisquam est, qui do<br>lorem ipsum quia dolor sit</p>
  </div>
</section>
<div class="divider"></div>

<h2 class="section-title featured-title heading">Featured Destinations</h2>
<div class="photo photo-resort" role="img" aria-label="Aerial view of a beachfront resort with white sand and turquoise water"></div>
<div class="photo photo-bay" role="img" aria-label="Coastal town beside a turquoise bay with mountains behind"></div>
<div class="photo photo-cove" role="img" aria-label="Green hillside overlooking a sheltered blue cove with boats"></div>
<div class="btn-outline explore">EXPLORE MORE</div>

<footer class="footer">
  <div class="contact-row">
    <div class="contact-item">
      <span class="icon-ring"><svg width="14" height="18" viewBox="0 0 24 30"><path d="M12 1a10 10 0 0 0-10 10c0 8 10 18 10 18s10-10 10-18A10 10 0 0 0 12 1z" fill="#fff"/><circle cx="12" cy="11" r="4" fill="#111"/></svg></span>
      <span>418 Harbor View Road<br>Tampa, FL 33602</span>
    </div>
    <div class="contact-item">
      <span class="icon-ring"><svg width="16" height="16" viewBox="0 0 24 24"><path d="M6.6 10.8a15.1 15.1 0 0 0 6.6 6.6l2.2-2.2c.3-.3.7-.4 1-.2 1.1.4 2.3.6 3.6.6.6 0 1 .4 1 1V20c0 .6-.4 1-1 1A17 17 0 0 1 3 4c0-.6.4-1 1-1h3.5c.6 0 1 .4 1 1 0 1.3.2 2.5.6 3.6.1.3 0 .7-.2 1z" fill="#fff"/></svg></span>
      <span>1 555 010 2040</span>
    </div>
    <div class="contact-item">
      <span class="icon-ring"><svg width="18" height="14" viewBox="0 0 24 18"><rect x="1" y="1" width="22" height="16" rx="1" fill="#fff"/><path d="M1 2l11 8 11-8" fill="none" stroke="#111" stroke-width="2"/></svg></span>
      <span>info@plotvista.com</span>
    </div>
  </div>
  <nav class="footer-nav">
    Home<span class="sep">|</span>About<span class="sep">|</span>Buy<span class="sep">|</span>Sell<span class="sep">|</span>Landlords<span class="sep">|</span>Rent<span class="sep">|</span>Our services<span class="sep">|</span>Contact
  </nav>
  <div class="footer-rule"></div>
  <p class="copyright">Copyrights © 2017, plotVista . All rights reserved.</p>
  <div class="social" aria-label="Social links"><span></span><span></span><span></span><span></span></div>
</footer>

</body>
</html>
```